Web design project for exciting Australian start-up

Background
We are looking for a creative and talented web design artist to work alongside our market leading web developer.
• You will be required to create a modern and clean design theme for our website, incorporating selected rustic colour scheme elements for our exciting Australian start-up to operate within the coffee industry.
reoccurring work to be expected to flow to the successful designer.
Requirements
• c. 5 - 10 page website
• Landing page
• Log in/ out
• 404 template
• Typography is emphasised
• Please use either a) typemarrow.com, b) free web fonts, c) brindle fonts
• All design elements in vector format
• Preferably with icons for each header title(i.e. about us, how it works etc) but designer have free reign over how the site looks, so might not be applicable
• All pages to be responsive
• Down to eSlab resolution

High level visual design brief attached - additional pages to be worked from base design.

Design inspiration
• We would like to use design elements from the following sources:
http://www.zandrix.com/halcyon/ (Functionality)
Colour scheme refer to logo and complementary style guide

```html
<!DOCTYPE html>
<html lang="en">
<head>
<meta charset="utf-8">
<title>Bean Meridian — Online Coffee Market Place</title>
<link rel="stylesheet" href="https://fonts.googleapis.com/css2?family=Oswald:wght@300;400;500;700&family=Inter:wght@300&family=Lato:wght@300;400&display=swap">
<style>
:root{
  --ink:#222;
  --ink-soft:#444;
  --muted:#666;
  --red:#e8394a;
  --red-btn:#e8333b;
  --orange:#f58a2c;
  --orange-deep:#ec6c12;
  --burlap-light:#e2d5ba;
  --burlap-dark:#c9b48e;
  --bean-dark:#4a2414;
  --bean-mid:#8a4424;
  --cup-light:#efebe5;
  --cup-shade:#e0dad1;
  --footer-bg:#ebebeb;
  --header-veil:rgba(255,255,255,.72);
  --btn-border:#cfcfcf;
}
*{box-sizing:border-box;margin:0;padding:0}
html,body{width:1200px;height:988px;overflow:hidden}
body{font-family:"Lato",sans-serif;color:var(--ink);background:#fff;position:relative}

/* Hero */
.hero{position:absolute;left:0;top:0;width:1200px;height:790px;
  background:radial-gradient(ellipse at 45% 35%,var(--burlap-light),var(--burlap-dark));}
.hero__cup{position:absolute;left:686px;top:223px;width:463px;height:338px;
  background:linear-gradient(160deg,var(--cup-light),var(--cup-shade));}
.hero__beans{position:absolute;left:0;top:527px;width:1200px;height:263px;
  background:linear-gradient(180deg,rgba(138,68,36,0) 0,var(--bean-mid) 22%,var(--bean-dark) 100%);}

/* Header */
.site-header{position:absolute;left:0;top:0;width:1200px;height:98px;background:var(--header-veil)}
.nav-btn{position:absolute;top:42px;height:29px;display:flex;align-items:center;justify-content:center;
  font-family:"Lato",sans-serif;font-size:12.5px;text-transform:uppercase;color:var(--ink-soft);
  background:#fafafa;border:1px solid var(--btn-border);text-decoration:none}
.nav-btn--home{left:52px;width:85px;background:var(--orange);border-color:var(--orange);color:#fff}
.nav-btn--about{left:147px;width:85px}
.nav-btn--how{left:943px;width:113px}
.nav-btn--login{left:1064px;width:84px;background:var(--red-btn);border-color:var(--red-btn);color:#fff;gap:6px}
.brand{position:absolute;left:0;top:37px;width:1200px;text-align:center;
  font-family:"Oswald",sans-serif;font-weight:700;font-size:27px;letter-spacing:1.5px;color:var(--ink);text-transform:uppercase}
.brand__dot{display:inline-block;width:22px;height:22px;border-radius:50%;background:var(--orange);vertical-align:-3px;margin:0 8px}

/* Headline */
.headline{position:absolute;left:69px;top:0;width:560px;height:420px;text-transform:uppercase;line-height:1}
.headline span{position:absolute;left:0;white-space:nowrap}
.headline__lead{top:229px;font-family:"Inter",sans-serif;font-weight:300;font-size:54px;letter-spacing:-3px;color:var(--ink-soft)}
.headline__main{top:279px;font-family:"Oswald",sans-serif;font-weight:700;font-size:70px;letter-spacing:2.5px;color:var(--red)}
.headline__sub{top:352px;font-family:"Oswald",sans-serif;font-weight:700;font-size:57px;letter-spacing:.5px;color:var(--orange-deep)}
.watch-btn{position:absolute;left:69px;top:445px;width:189px;height:43px;border:1px solid #b9ad97;
  background:rgba(255,255,255,.25);display:flex;align-items:center;gap:14px;padding-left:24px;
  font-family:"Oswald",sans-serif;font-weight:500;font-size:19px;color:var(--ink-soft);text-transform:uppercase;text-decoration:none}

/* Footer */
.site-footer{position:absolute;left:0;top:790px;width:1200px;height:198px;background:var(--footer-bg)}
.footer-col{position:absolute;top:33px}
.footer-col h3{font-family:"Lato",sans-serif;font-weight:400;font-size:14px;text-transform:uppercase;color:#111;margin-bottom:10px}
.footer-col ul{list-style:none}
.footer-col li{font-family:"Lato",sans-serif;font-weight:300;font-size:13.5px;line-height:20.3px;color:#333}
.footer-col--about{left:51px;width:305px}
.footer-col--about p{font-weight:300;font-size:11.6px;line-height:16.7px;color:var(--muted)}
.footer-col--help{left:429px}
.footer-col--who{left:618px}
.footer-col--follow{left:788px}
.social li{display:flex;align-items:center;gap:10px;height:26.7px;font-size:14px}
.social__icon{width:18px;height:18px;border-radius:50%;background:#9a9a9a}
.footer-brand{position:absolute;left:930px;top:70px;width:250px;text-align:center}
.footer-brand__name{font-family:"Oswald",sans-serif;font-weight:700;font-size:20px;letter-spacing:1px;color:#666;text-transform:uppercase}
.footer-brand__copy{font-size:13px;color:#444;margin-top:22px}
</style>
</head>
<body>

<section class="hero">
  <div class="hero__cup" role="img" aria-label="Photo of a cup of black coffee on a saucer with scattered beans"></div>
  <div class="hero__beans" role="img" aria-label="Photo of roasted coffee beans piled along the bottom edge on burlap"></div>

  <h1 class="headline">
    <span class="headline__lead">Australia’s First</span>
    <span class="headline__main">Online Coffee</span>
    <span class="headline__sub">Market Place</span>
  </h1>

  <a class="watch-btn" href="#">
    <svg width="14" height="16" viewBox="0 0 14 16" aria-hidden="true"><path d="M1 1 L13 8 L1 15 Z" fill="var(--red)"/></svg>
    Watch Video
  </a>
</section>

<header class="site-header">
  <a class="nav-btn nav-btn--home" href="#">Home</a>
  <a class="nav-btn nav-btn--about" href="#">About Us</a>
  <div class="brand">Bean<span class="brand__dot"></span>Meridian</div>
  <a class="nav-btn nav-btn--how" href="#">How It Works</a>
  <a class="nav-btn nav-btn--login" href="#">
    <svg width="13" height="14" viewBox="0 0 13 14" aria-hidden="true"><circle cx="6.5" cy="4" r="3.5" fill="#fff"/><path d="M0 14 C0 9 13 9 13 14 Z" fill="#fff"/></svg>
    Login
  </a>
</header>

<footer class="site-footer">
  <div class="footer-col footer-col--about">
    <h3>About Us</h3>
    <p>Lorem ipsum dolor sit amet, consectetur adipisicing elit, sed do eiusmod tempor incididunt ut labore et dolore magna aliqua. Ut enim ad minim veniam, quis nostrud exercitation ullamco laboris nisi ut aliquip ex ea commodo consequat. Duis aute irure dolor in reprehenderit in voluptate velit esse cillum dolore eu fugiat nulla pariatur.</p>
  </div>
  <div class="footer-col footer-col--help">
    <h3>Helpful Info</h3>
    <ul><li>About us</li><li>Media Enquiries</li><li>Terms &amp; Conditions</li><li>Privacy Policy</li></ul>
  </div>
  <div class="footer-col footer-col--who">
    <h3>Who We Are</h3>
    <ul><li>How It Works</li><li>Faq</li><li>Contact Us</li></ul>
  </div>
  <div class="footer-col footer-col--follow">
    <h3>Follow Us</h3>
    <ul class="social">
      <li><span class="social__icon"></span>Friendwall</li>
      <li><span class="social__icon"></span>Workring</li>
      <li><span class="social__icon"></span>Friendwall</li>
      <li><span class="social__icon"></span>Workring</li>
    </ul>
  </div>
  <div class="footer-brand">
    <div class="footer-brand__name">Bean Meridian</div>
    <div class="footer-brand__copy">Copyright © 2014 Bean Meridian.</div>
  </div>
</footer>

</body>
</html>
```